Web Design Project

i'm looking for a sleek modern design i can use for a web site that deals with.
Intelligent Data Capture
Accounts Payable Solutions for faster processing based on our scanning solution.
ultimately we are a intelligent scanning software.

here is a great website, that does exactly what we do, and we like to have most of their services and products.

so something in this idea would be great.
www.valtrino.com

so i guess i want a good landing/home page which is smartly designed so users will be inclined to leave their information.

and then information pages.

also i dont need any cms for you to include, i only need you to hook the html hooks for RANK Kettle as i already have a CMS and need it to hook in to that, i am including links to that cheat sheet.
so it is easier when included as you create the Theme.

http://www.rankkettle.com/how-to-create-website-template.html
http://www.rankkettle.com/cheat-sheet.html
Updates

Hi Guys sorry for the long pause in design, but here is where we stand.

what ever design i choose, i need that designer to customize a few things for me based on design that was designed.
and i will need designer to match that them to work with RANK Kettle
here is the cheat sheet for the hooks that we need to match and make it work.
if you have any questions let me know.

otherwise i look forward to working with you. and good luck.

Target Market(s)

CFO's AP Managers, mostly ppl who are not Tech freindly

Industry/Entity Type

Software

Requirements
Must have
• i need on home page, the rotating banner should have 1 ability to place youtube links to show videos, and also ability to add buttons on these rotating banners that will allow forms to pop up take to another page.

```html
<!DOCTYPE html>
<html lang="en">
<head>
<meta charset="utf-8">
<title>VARDO — Intelligent Data Capture</title>
<link href="https://fonts.googleapis.com/css2?family=Yanone+Kaffeesatz:wght@300;400&family=Arimo:wght@400;700&display=swap" rel="stylesheet">
<style>
:root{
  --blue:#2a73e0;
  --blue-light:#6fb0ef;
  --blue-mid:#3b8be0;
  --ink:#111;
  --text:#444;
  --muted:#555;
  --line:#d8d8d8;
  --panel:#fff;
  --btn-top:#6a6a6a;
  --btn-bot:#3a3a3a;
  --foot-top:#3d3d3d;
  --foot-bot:#121212;
  --foot-text:#e8e8e8;
}
*{box-sizing:border-box;margin:0;padding:0}
html,body{width:908px;height:1200px;overflow:hidden;background:#fff}
body{position:relative;font-family:"Arimo",Arial,sans-serif;color:var(--text)}
.abs{position:absolute}
.logo{left:62px;top:10px;font:400 46px/1 "Arimo",Arial,sans-serif;color:var(--ink);letter-spacing:1px}
.nav{left:268px;top:36px;width:570px;height:34px}
.nav ul{position:absolute;left:30px;top:0;right:12px;height:34px;display:flex;justify-content:space-between;align-items:center;list-style:none}
.nav li{font:400 12.5px/1 "Yanone Kaffeesatz",sans-serif;color:#fff;letter-spacing:.3px;text-transform:uppercase}
.nav li.sep{width:1px;height:10px;background:#dbe9fb}
.band{left:0;top:70px;width:908px;height:323px;background:var(--blue)}
.slider-frame{left:64px;top:92px;width:774px;height:301px;background:#e9eef4}
.slide{left:70px;top:97px;width:762px;height:296px;background:linear-gradient(180deg,#f6f7f9 0%,#dfe6ef 45%,#7f98b8 100%)}
.arrow{top:214px;width:16px;height:40px}
.pager{left:405px;top:378px;width:121px;height:28px;background:#f3f3f3;border-radius:5px;box-shadow:0 1px 2px rgba(0,0,0,.15);display:flex;align-items:center;justify-content:center;gap:4px}
.pager .dot{width:11px;height:11px;border-radius:50%;background:#8a8a8a;border:2px solid #bdbdbd}
.pager .dot.on{background:#c9c9c9;border-color:#888}
.pager svg{margin:0 7px}
.box{top:424px;width:247px;height:344px;border:1px solid var(--line);border-radius:10px;background:linear-gradient(180deg,#fff 78%,#ececec 100%);box-shadow:0 6px 6px -6px rgba(0,0,0,.25)}
.box .tab{position:absolute;left:-1px;top:-1px;width:247px;height:36px}
.box h2{position:absolute;left:38px;top:8px;font:400 19px/1 "Yanone Kaffeesatz",sans-serif;color:#fff;text-transform:uppercase}
.media{position:absolute}
.btn{position:absolute;width:50px;height:24px;border-radius:6px;background:linear-gradient(180deg,var(--btn-top),var(--btn-bot));color:#fff;font:400 15px/24px "Yanone Kaffeesatz",sans-serif;text-align:center;box-shadow:0 1px 2px rgba(0,0,0,.3)}
.title{font:700 10.5px/1 Arial,sans-serif;color:#333}
.copy{font:400 8.8px/13.6px Arial,sans-serif;color:var(--muted)}
.svc-list{list-style:none;position:absolute;left:50px;top:166px}
.svc-list li{font:400 10.5px/22.8px Arial,sans-serif;color:#333;position:relative}
.svc-list li.mk::before{content:"";position:absolute;left:-9px;top:8px;border-left:4px solid var(--blue-mid);border-top:3px solid transparent;border-bottom:3px solid transparent}
.welcome{left:64px;top:790px;width:771px;height:161px;border:1px solid var(--line);border-radius:8px;background:linear-gradient(180deg,#fff 80%,#efefef 100%)}
.welcome h2{position:absolute;left:193px;top:14px;font:300 20px/1 "Yanone Kaffeesatz",sans-serif;color:#333;text-transform:uppercase}
.welcome .rule{position:absolute;left:193px;top:39px;width:560px;height:1px;background:#cfcfcf}
.welcome p{position:absolute;left:193px;top:52px;width:570px;font:400 8.6px/16.8px Arial,sans-serif;color:#444}
.footer{left:0;top:973px;width:908px;height:227px;background:linear-gradient(180deg,var(--foot-top),var(--foot-bot));color:var(--foot-text)}
.footer h3{position:absolute;font:400 18.5px/1 Arial,sans-serif;color:#f2f2f2}
.vsep{position:absolute;top:10px;width:1px;height:175px;background:#5a5a5a}
.field{position:absolute;left:283px;width:181px;background:#fff;font:400 9px/1 Arial,sans-serif;color:#333;padding:7px 8px}
.links{position:absolute;left:497px;top:57px;list-style:none}
.links li{font:400 9px/16px Arial,sans-serif;color:#fff;position:relative;padding-left:11px}
.links li::before{content:"";position:absolute;left:0;top:5px;width:4px;height:4px;border-right:1.3px solid #fff;border-top:1.3px solid #fff;transform:rotate(45deg)}
.social{position:absolute;top:1046px;width:30px;height:30px;border-radius:50%;background:#8a8a8a}
.bottom{left:64px;top:1171px;width:771px;height:29px;background:#505050;color:#ddd;font:400 9px/29px Arial,sans-serif;text-align:center}
</style>
</head>
<body>

<div class="abs logo">VARDO</div>

<nav class="abs nav">
  <svg width="570" height="34" viewBox="0 0 570 34" style="position:absolute;left:0;top:0">
    <defs><linearGradient id="navg" x1="0" y1="0" x2="0" y2="1"><stop offset="0" stop-color="#7cbaf0"/><stop offset="1" stop-color="#2f7fde"/></linearGradient></defs>
    <path d="M0 34 C14 34 18 28 22 16 C26 4 30 0 42 0 H558 Q570 0 570 12 V34 Z" fill="url(#navg)"/>
  </svg>
  <ul>
    <li>Home</li><li class="sep"></li><li>About Us</li><li class="sep"></li><li>Services</li><li class="sep"></li><li>Gallery</li><li class="sep"></li><li>Blog</li><li class="sep"></li><li>Testimonials</li><li class="sep"></li><li>Contact Us</li>
  </ul>
</nav>

<div class="abs band"></div>
<div class="abs slider-frame"></div>
<div class="abs slide" role="img" aria-label="Banner photo of a smiling business team with a desktop document scanner"></div>
<svg class="abs arrow" style="left:30px" viewBox="0 0 16 40"><path d="M14 2 L3 20 L14 38" fill="none" stroke="#fff" stroke-width="1.5"/></svg>
<svg class="abs arrow" style="left:854px" viewBox="0 0 16 40"><path d="M2 2 L13 20 L2 38" fill="none" stroke="#fff" stroke-width="1.5"/></svg>
<div class="abs pager">
  <svg width="8" height="11" viewBox="0 0 8 11"><path d="M6 1 L2 5.5 L6 10" fill="none" stroke="#444" stroke-width="1.8"/></svg>
  <span class="dot on"></span><span class="dot"></span><span class="dot"></span><span class="dot"></span>
  <svg width="8" height="11" viewBox="0 0 8 11"><path d="M2 1 L6 5.5 L2 10" fill="none" stroke="#444" stroke-width="1.8"/></svg>
</div>

<svg width="0" height="0" style="position:absolute">
  <defs><linearGradient id="tabg" x1="0" y1="0" x2="0" y2="1"><stop offset="0" stop-color="#7cbaf0"/><stop offset="1" stop-color="#2f7fde"/></linearGradient></defs>
</svg>

<section class="abs box" style="left:64px">
  <svg class="tab" viewBox="0 0 247 36"><path d="M0 36 C12 36 16 30 19 18 C22 5 26 0 38 0 H237 Q247 0 247 10 V36 Z" fill="url(#tabg)"/></svg>
  <h2>How it works</h2>
  <div class="media" style="left:16px;top:49px;width:214px;height:178px;background:linear-gradient(180deg,#6f8a80,#a9b7ae 70%,#cfd3d6);border:3px solid #1f6fb7" role="img" aria-label="Video preview of a presenter beside a chalkboard"></div>
  <div class="abs title" style="left:18px;top:243px">Title Comes Here</div>
  <p class="abs copy" style="left:18px;top:256px;width:215px">Tempor incididunt ut labore et dolore magna aliqua. Ut enim ad minim veniam, quis nostrud exercitation ullamco laboris nisi ut aliquip...</p>
  <div class="btn" style="left:176px;top:297px">More</div>
</section>

<section class="abs box" style="left:330px">
  <svg class="tab" viewBox="0 0 247 36"><path d="M0 36 C12 36 16 30 19 18 C22 5 26 0 38 0 H237 Q247 0 247 10 V36 Z" fill="url(#tabg)"/></svg>
  <h2>Services</h2>
  <div class="media" style="left:19px;top:51px;width:210px;height:102px;background:linear-gradient(135deg,#3a3d44,#8a8580 55%,#4a5a80)" role="img" aria-label="Photo of people working at computer monitors"></div>
  <ul class="svc-list">
    <li class="mk">Lorem Lipsum</li><li class="mk">Lorem Lipsum</li><li class="mk">Lorem Lipsum</li><li class="mk">Lorem Lipsum</li><li>Lorem Lipsum</li>
  </ul>
  <div class="btn" style="left:177px;top:297px">More</div>
</section>

<section class="abs box" style="left:588px">
  <svg class="tab" viewBox="0 0 247 36"><path d="M0 36 C12 36 16 30 19 18 C22 5 26 0 38 0 H237 Q247 0 247 10 V36 Z" fill="url(#tabg)"/></svg>
  <h2>Latest News</h2>
  <div class="media" style="left:19px;top:51px;width:211px;height:102px;background:linear-gradient(90deg,#b9c3cf,#e2d8cf 45%,#2d3a5a 70%,#8f2a2a)" role="img" aria-label="Photo of a businessman in an office"></div>
  <div class="abs title" style="left:19px;top:172px">Jan 04, 2013</div>
  <p class="abs copy" style="left:19px;top:185px;width:215px">Tempor incididunt ut labore et dolore magna aliqua. Ut enim ad minim veniam, quis nostrud exercitation ullamco laboris nisi ut aliquip...</p>
  <div class="abs title" style="left:19px;top:237px">Jan 04, 2013</div>
  <p class="abs copy" style="left:19px;top:250px;width:215px">Tempor incididunt ut labore et dolore magna aliqua. Ut enim ad minim veniam, quis nostrud exercitation ullamco laboris nisi ut aliquip...</p>
  <div class="btn" style="left:185px;top:297px">More</div>
</section>

<section class="abs welcome">
  <div class="media" style="left:14px;top:13px;width:160px;height:131px;background:linear-gradient(180deg,#8d9199,#2a2c31 60%,#1c1d20)" role="img" aria-label="Photo of an open flatbed document scanner"></div>
  <h2>Welcome to our site</h2>
  <div class="rule"></div>
  <p>Lorem ipsum dolor sit amet, consectetur adipisicing elit, sed do eiusmod tempor incididunt ut labore et dolore magna aliqua. Ut enim ad minim veniam, quis nostrud exercitation ullamco laboris nisi ut aliquip ex ea commodo consequat. Duis aute irure dolor in reprehenderit in voluptate velit esse cillum dolore eu fugiat nulla pariatur. Excepteur sint occaecat cupidatat non proident, sunt in culpa qui officia deserunt mollit anim id est laborum."</p>
  <div class="btn" style="left:701px;top:119px">More</div>
</section>

<footer class="abs footer">
  <h3 style="left:64px;top:27px">Call Today</h3>
  <div class="abs" style="left:64px;top:52px;font:400 13.5px/1 Arial,sans-serif;color:#eee">For a Free Consultation</div>
  <div class="abs" style="left:64px;top:79px;font:700 18.5px/1 Arial,sans-serif;color:#fff">123 456 7890</div>
  <div class="vsep" style="left:263px"></div>
  <h3 style="left:283px;top:27px">Contact Information</h3>
  <div class="field" style="top:59px;height:23px">Name</div>
  <div class="field" style="top:92px;height:56px">Message</div>
  <div class="btn" style="left:283px;top:160px;width:50px;background:linear-gradient(180deg,#3a3a3a,#0c0c0c);border:1px solid #555">Submit</div>
  <div class="vsep" style="left:475px"></div>
  <h3 style="left:495px;top:27px">Quick Links</h3>
  <ul class="links">
    <li>Home</li><li>About Us</li><li>Services</li><li>Gallery</li><li>Blog</li><li>Testimonial</li><li>Contact Us</li>
  </ul>
  <div class="vsep" style="left:642px"></div>
  <h3 style="left:663px;top:27px">Follow us on</h3>
</footer>
<div class="social" style="left:663px" aria-label="Social profile"></div>
<div class="social" style="left:700px" aria-label="Social profile"></div>
<div class="social" style="left:737px" aria-label="Social profile"></div>

<div class="abs bottom">Copyrights © 2012. All Rights Reserved.</div>

</body>
</html>
```